Blow Dry Bar Business Cards

These cards must be eye catching and modern.
You must be willing to work fast and make changes.

Winner will be offered other projects

Files 1 THIS IS THE STYLE CARDS I AM INTRESTED IN!!!
Please be creative, I am paying for my own eye catching design. I need files to be nexa press ready.

COLORS THAT ARE PAINTED INSIDE MY SHOP:
- - - http://www.quorvelpaint.example/en/explore-colors/painter/color-selector.html?colors=4007-3C

- - - http://www.brandivex.example/color/paint-colors/hidden-corridor-d58-2

I want the business cards sleek and modern if you use the logo please correct imperfections. I added the part that says Blow Dry Bar (see website).
Do not be afraid to separate the blow dryer from the name to make the cards look like the file with the pink elephant.

SHOULD INCLUDE
*Blow Dryer (we are a blow dry bar not a salon we do not cut or color so do not include sheers of any kind)
*BUSINESS NAME: Simply Swept Upward - Blow Dry Bar (PLEASE SEE MY WEBSITE)
* Website: SIMPLYSWEPTUPWARD.EXAMPLE
*Phone number (555) 014-2763
Updates

Nexa press said it can be submitted in JPG

http://www.brandivex.example/color/paint-colors/hidden-corridor-d58-2 http://www.quorvelpaint.example/en/explore-colors/painter/color-selector.html?colors=4007-3C ^^^^ These links will take you to the color paint that is painted inside my shop.

Target Market(s)

AGES 18 - 55 WOMEN
HIGH END MARKET

Industry/Entity Type

Salon

Requirements
Must have
• SEE COLOR EXAMPLE FILE
BLOW DRYER
UNIQUE
I LIKE THE CARD WITH THE PINK ELEPHANT THE BEST
Nice to have
• BE AS CREATIVE AND MODERN AS POSSIBLE DO NOT COPY ANY OF THE CARDS BELOW.
Should not have
• SCISSORS
PINK

```html
<!DOCTYPE html>
<html lang="en">
<head>
<meta charset="utf-8">
<title>Swept Upward – Blow Dry Bar Business Cards</title>
<link rel="stylesheet" href="https://fonts.googleapis.com/css2?family=Arvo&family=Questrial&display=swap">
<style>
  :root {
    --backdrop: #1d1d1f;
    --card: #050505;
    --card-edge: #151515;
    --teal: #4fc3c9;
    --mauve: #6e4c58;
    --mauve-dim: #4a333c;
    --photo-top: #f3dde3;
    --photo-mid: #c9b8a4;
    --photo-low: #7d8a58;
  }
  * { box-sizing: border-box; margin: 0; padding: 0; }
  html, body { width: 1200px; height: 800px; overflow: hidden; }
  body { background: var(--backdrop); position: relative; font-family: "Questrial", sans-serif; }

  .card {
    position: absolute;
    width: 500px;
    height: 290px;
    border-radius: 22px;
    background: var(--card);
    box-shadow: 0 0 0 1px var(--card-edge);
    overflow: hidden;
  }

  /* Front card */
  .card--front { left: 90px; top: 120px; }
  .front__photo {
    position: absolute;
    right: 0; top: 0;
    width: 230px; height: 100%;
    background: linear-gradient(180deg, var(--photo-top) 0%, var(--photo-mid) 55%, var(--photo-low) 100%);
  }
  .front__fade {
    position: absolute;
    right: 230px; top: 0;
    width: 60px; height: 100%;
    background: linear-gradient(270deg, rgba(5,5,5,0) 0%, var(--card) 100%);
  }
  .front__fade--inner {
    right: 170px;
    background: linear-gradient(90deg, var(--card) 0%, rgba(5,5,5,0) 100%);
  }
  .front__brand {
    position: absolute;
    left: 30px; top: 180px;
    display: flex; align-items: center; gap: 8px;
  }
  .front__mark {
    width: 16px; height: 16px;
    border-radius: 50%;
    background: var(--mauve-dim);
  }
  .front__name {
    font-family: "Arvo", serif;
    font-size: 20px;
    line-height: 1;
    color: var(--mauve-dim);
  }

  /* Back card */
  .card--back { left: 610px; top: 390px; }
  .back__brand {
    position: absolute;
    right: 34px; top: 36px;
    text-align: right;
  }
  .back__lockup {
    display: flex; align-items: center; justify-content: flex-end; gap: 12px;
  }
  .back__mark {
    width: 34px; height: 34px;
    border-radius: 50%;
    background: var(--teal);
  }
  .back__name {
    font-family: "Arvo", serif;
    font-size: 38px;
    line-height: 1;
    color: var(--teal);
  }
  .back__tagline {
    margin-top: 8px;
    font-size: 21px;
    line-height: 1.1;
    color: var(--mauve);
  }
  .back__descriptor {
    font-size: 15px;
    line-height: 1.3;
    color: var(--mauve);
  }
  .back__site-top {
    position: absolute;
    right: 34px; top: 172px;
    font-size: 15px;
    letter-spacing: 0.5px;
    color: var(--mauve);
  }
  .back__contact {
    position: absolute;
    left: 28px; bottom: 24px;
    list-style: none;
    font-size: 15px;
    color: var(--mauve);
  }
  .back__contact li { display: flex; align-items: center; gap: 10px; margin-top: 6px; }
  .back__contact svg { width: 16px; height: 16px; fill: none; stroke: var(--teal); stroke-width: 1.8; }
</style>
</head>
<body>
  <section class="card card--front" aria-label="Business card front">
    <div class="front__photo" role="img" aria-label="Photograph of four women in casual western wear standing together in a grassy field"></div>
    <div class="front__fade"></div>
    <div class="front__brand">
      <span class="front__mark" aria-hidden="true"></span>
      <p class="front__name">Swept Upward</p>
    </div>
  </section>

  <section class="card card--back" aria-label="Business card back">
    <div class="back__brand">
      <div class="back__lockup">
        <span class="back__mark" aria-hidden="true"></span>
        <p class="back__name">Swept Upward</p>
      </div>
      <p class="back__tagline">Simply Swept Upward</p>
      <p class="back__descriptor">Blow Dry Bar</p>
    </div>
    <p class="back__site-top">SIMPLYSWEPTUPWARD.EXAMPLE</p>
    <ul class="back__contact">
      <li>
        <svg viewBox="0 0 16 16" aria-hidden="true"><path d="M3 2h3l1.5 3.5-2 1.2a8 8 0 0 0 3.8 3.8l1.2-2L14 10v3a1 1 0 0 1-1 1A11 11 0 0 1 2 3a1 1 0 0 1 1-1z"/></svg>
        <span>(555) 014-2763</span>
      </li>
      <li>
        <svg viewBox="0 0 16 16" aria-hidden="true"><circle cx="8" cy="8" r="6.2"/><ellipse cx="8" cy="8" rx="2.6" ry="6.2"/><path d="M1.8 8h12.4"/></svg>
        <span>WWW.SIMPLYSWEPTUPWARD.EXAMPLE</span>
      </li>
    </ul>
  </section>
</body>
</html>
```